Business cards to launch an education platform

Hi,
I am looking at having new business cards designed.
I am a startup, developing a web platform for schools and university, the education world. It's an online assessment system.
I would like a card that looks classy, and that is using the colors and the font of my logo.

I have attached:
1) my logo
2) A business card that I have designed quickly so you can have all the information required in the card, but I really don't like it.
3) The font that I am using (Lato Regular) to design my web platform
4) Some screenshots of my web platform so you can have a look at the style that I have.

Target Market(s)

Major market: Education system: Schools and university
Minor markets: Business in general

Industry/Entity Type

Business

Contact Information for Business Card

Clara Fenwick
Director

M: 0437 518 902
E: clara.fenwick@amberLoomSystems.com.au

Requirements
Must have
• The colors of my logo

```html
<!DOCTYPE html>
<html lang="en">
<head>
<meta charset="utf-8">
<title>Amber Loom Systems – Business Cards</title>
<link rel="stylesheet" href="https://fonts.googleapis.com/css2?family=Lato:wght@300;400;700&display=swap">
<style>
  :root {
    --bg: #e9ecf0;
    --card-white: #ffffff;
    --navy: #0d3f86;
    --royal: #1560b5;
    --sky: #2fb3ea;
    --deep: #08306b;
    --grey-text: #4a5563;
    --shadow: rgba(10, 30, 60, 0.18);
  }
  * { margin: 0; padding: 0; box-sizing: border-box; }
  html, body {
    width: 1200px;
    height: 950px;
    overflow: hidden;
    background: var(--bg);
    font-family: "Lato", Arial, sans-serif;
  }
  .canvas {
    position: relative;
    width: 1200px;
    height: 950px;
  }
  .card {
    position: absolute;
    left: 250px;
    width: 700px;
    height: 428px;
    border-radius: 4px;
    overflow: hidden;
    box-shadow: 0 10px 28px var(--shadow);
  }
  /* Front */
  .card-front { top: 34px; background: var(--card-white); }
  .front-band { position: absolute; left: 0; top: 0; width: 700px; height: 428px; }
  .brand {
    position: absolute;
    left: 64px;
    top: 128px;
    display: flex;
    align-items: center;
    gap: 16px;
  }
  .brand-square {
    width: 62px;
    height: 62px;
    background: var(--royal);
  }
  .brand-name {
    font-weight: 400;
    font-size: 30px;
    letter-spacing: 2px;
    color: var(--royal);
    text-transform: uppercase;
    line-height: 1;
  }
  .person {
    position: absolute;
    left: 142px;
    top: 214px;
  }
  .person-name {
    font-weight: 700;
    font-size: 24px;
    letter-spacing: 1px;
    color: var(--navy);
    text-transform: uppercase;
  }
  .person-role {
    margin-top: 4px;
    font-size: 14px;
    letter-spacing: 1.5px;
    color: var(--sky);
    text-transform: uppercase;
  }
  .contact-list {
    list-style: none;
    margin-top: 16px;
  }
  .contact-item {
    display: flex;
    align-items: center;
    gap: 10px;
    font-size: 15px;
    color: var(--grey-text);
    margin-bottom: 6px;
  }
  .contact-icon { width: 16px; height: 16px; flex: none; }

  /* Back */
  .card-back {
    top: 488px;
    background: linear-gradient(135deg, var(--deep) 0%, var(--royal) 55%, #1f86d6 100%);
  }
  .back-pattern {
    position: absolute;
    inset: 0;
    background: radial-gradient(circle at 50% 50%, rgba(80, 170, 240, 0.35) 0%, rgba(80, 170, 240, 0) 60%);
  }
  .back-web {
    position: absolute;
    left: 34px;
    top: 28px;
    font-size: 16px;
    letter-spacing: 0.5px;
    color: #ffffff;
  }
  .back-brand {
    position: absolute;
    left: 50%;
    top: 50%;
    transform: translate(-50%, -50%);
    display: flex;
    align-items: center;
    gap: 16px;
  }
  .back-brand .brand-square { background: #ffffff; width: 56px; height: 56px; }
  .back-brand .brand-name { color: #ffffff; font-size: 28px; }
</style>
</head>
<body>
<main class="canvas">

  <section class="card card-front" aria-label="Business card front">
    <svg class="front-band" viewBox="0 0 700 428" aria-hidden="true">
      <path d="M0 352 H556 L578 330 H644 L666 352 H700 V362 H662 L640 340 H582 L560 362 H0 Z" fill="var(--sky)"/>
      <path d="M0 366 H562 L584 344 H638 L660 366 H700 V428 H0 Z" fill="var(--royal)"/>
    </svg>

    <div class="brand">
      <div class="brand-square"></div>
      <div class="brand-name">Amber Loom Systems</div>
    </div>

    <div class="person">
      <div class="person-name">Clara Fenwick</div>
      <div class="person-role">Director</div>
      <ul class="contact-list">
        <li class="contact-item">
          <svg class="contact-icon" viewBox="0 0 16 16" aria-hidden="true">
            <rect x="4" y="1" width="8" height="14" rx="1.5" fill="none" stroke="var(--navy)" stroke-width="1.5"/>
            <circle cx="8" cy="12.3" r="0.9" fill="var(--navy)"/>
          </svg>
          <span>0437 518 902</span>
        </li>
        <li class="contact-item">
          <svg class="contact-icon" viewBox="0 0 16 16" aria-hidden="true">
            <rect x="1" y="3" width="14" height="10" rx="1" fill="none" stroke="var(--navy)" stroke-width="1.5"/>
            <path d="M1.5 3.8 L8 9 L14.5 3.8" fill="none" stroke="var(--navy)" stroke-width="1.5"/>
          </svg>
          <span>clara.fenwick@amberLoomSystems.com.au</span>
        </li>
      </ul>
    </div>
  </section>

  <section class="card card-back" aria-label="Business card back">
    <div class="back-pattern" role="img" aria-label="Faint repeating brand pattern on blue background"></div>
    <div class="back-web">www.amberLoomSystems.com.au</div>
    <div class="back-brand">
      <div class="brand-square"></div>
      <div class="brand-name">Amber Loom Systems</div>
    </div>
  </section>

</main>
</body>
</html>
```